Summit Ridge Business Card

Side 1: Summit Ridge Logo (logo without Maltese cross) with industrial rope rescue related theme. Our company services - TRAINING - Fire Training, Confined Space Rescue Training, Rope Rescue training, Hazmat Training, Incident Command, EMS, Pump Operations Training. Website - summitridgeexample.com.
Side 2: Summit Ridge Fire Department Logo (logo with Maltese cross) with Firefighter related theme. Company (division) services - FIELD SERVICES - Fire Department, Stand-by Rescue, Safety, EMS, Planning. "Supporting the Emergency Response Community Since 1967"

Add contact information wherever it makes since (Name, Email, Phone).
I would like it to represent the Summit Ridge Fire Department Logo as a division not as a separate entity without saying it, possibly by depicting it in the background of Side 2 instead of being a standalone picture like the logo on Side 1.

```html
<!DOCTYPE html>
<html lang="en">
<head>
<meta charset="utf-8">
<title>Summit Ridge Business Card</title>
<link rel="stylesheet" href="https://fonts.googleapis.com/css2?family=Poppins:wght@400;500;600;700&family=Montserrat:wght@800;900&display=swap">
<style>
  :root {
    --canvas-bg: #2a2a2a;
    --field-red: #e80000;
    --field-red-deep: #d60000;
    --training-dark: #1f1f1f;
    --training-dark-2: #262626;
    --ink-white: #ffffff;
    --accent-red: #ee1111;
  }
  * { margin: 0; padding: 0; box-sizing: border-box; }
  html, body {
    width: 1200px; height: 1108px; overflow: hidden;
    background: var(--canvas-bg);
  }
  .canvas {
    position: relative; width: 1200px; height: 1108px;
    display: flex; justify-content: center; align-items: center; gap: 70px;
  }
  .card {
    position: relative; width: 410px; height: 700px;
    border-radius: 26px; overflow: hidden;
    box-shadow: 0 18px 40px rgba(0,0,0,.45);
    font-family: "Poppins", sans-serif; color: var(--ink-white);
    text-align: center;
  }
  .card-pattern { position: absolute; inset: 0; }
  .card--field .card-pattern {
    background: radial-gradient(circle at 50% 40%, var(--field-red) 0%, var(--field-red-deep) 100%);
  }
  .card--training .card-pattern {
    background: radial-gradient(circle at 50% 30%, var(--training-dark-2) 0%, var(--training-dark) 100%);
  }
  .card-body {
    position: relative; height: 100%;
    display: flex; flex-direction: column; align-items: center;
  }

  /* Field services side */
  .card--field .card-body { padding-top: 108px; }
  .section-title {
    font-weight: 600; font-size: 42px; letter-spacing: 1px; line-height: 1.1;
  }
  .card--field .section-title { margin-bottom: 18px; }
  .service-list { list-style: none; font-weight: 500; text-transform: uppercase; }
  .card--field .service-list { font-size: 25px; line-height: 1.28; }
  .rule-short { width: 58px; height: 2px; background: var(--ink-white); margin: 26px 0; }
  .contact-name {
    font-family: "Montserrat", sans-serif; font-weight: 800; font-size: 38px;
    margin-top: -4px; margin-bottom: 20px;
  }
  .contact-line { font-size: 22px; line-height: 1.35; font-weight: 400; }
  .tagline { font-size: 18px; line-height: 1.35; font-weight: 500; }

  /* Training side */
  .card--training .card-body { padding-top: 130px; }
  .brand-lockup { display: flex; align-items: center; gap: 12px; margin-bottom: 12px; }
  .brand-dot { width: 18px; height: 18px; border-radius: 50%; background: var(--accent-red); }
  .brand-name {
    font-family: "Montserrat", sans-serif; font-weight: 900; font-size: 42px;
    color: var(--accent-red); letter-spacing: 1px; text-transform: uppercase;
  }
  .brand-rule { width: 330px; height: 3px; background: var(--accent-red); margin-bottom: 56px; }
  .card--training .section-title {
    font-family: "Montserrat", sans-serif; font-weight: 800; font-size: 46px;
    color: var(--accent-red); margin-bottom: 10px;
  }
  .card--training .service-list { font-size: 20px; line-height: 1.32; }
  .rule-long { width: 340px; height: 2px; background: var(--accent-red); margin: 30px 0 22px; }
  .website { font-size: 24px; font-weight: 400; letter-spacing: .5px; }
  .website-domain { color: var(--accent-red); }
</style>
</head>
<body>
<main class="canvas">

  <section class="card card--field">
    <div class="card-pattern" role="img" aria-label="Faint repeating division emblem pattern across the red background"></div>
    <div class="card-body">
      <h2 class="section-title">FIELD SERVICES</h2>
      <ul class="service-list">
        <li>Fire Department</li>
        <li>Stand-by Rescue</li>
        <li>Safety</li>
        <li>EMS</li>
        <li>Planning</li>
      </ul>
      <div class="rule-short"></div>
      <p class="contact-name">Daniel Hartwell</p>
      <p class="contact-line">044-555 010 246</p>
      <p class="contact-line">info@summitridge.com</p>
      <div class="rule-short"></div>
      <p class="tagline">Supporting the Emergency Response<br>Community Since 1967</p>
    </div>
  </section>

  <section class="card card--training">
    <div class="card-pattern" role="img" aria-label="Faint repeating emblem pattern across the dark background"></div>
    <div class="card-body">
      <div class="brand-lockup">
        <span class="brand-dot"></span>
        <span class="brand-name">Summit Ridge</span>
      </div>
      <div class="brand-rule"></div>
      <h2 class="section-title">TRAINING</h2>
      <ul class="service-list">
        <li>Fire Training</li>
        <li>Confined Space Rescue Training</li>
        <li>Rope Rescue Training</li>
        <li>Hazmat Training</li>
        <li>Incident Command</li>
        <li>EMS</li>
        <li>Pump Operations Training</li>
      </ul>
      <div class="rule-long"></div>
      <p class="website">www.<span class="website-domain">summitridgeexample</span>.com</p>
    </div>
  </section>

</main>
</body>
</html>
```